Business Card Design

We need a business card designed for our new company. Prefer a black card with white logo & writing.

Contact Information for Business Card

Ted Galloway, address: 7-4812 Fernhollow Road, Abbotsford, BC, V3K 8R2, Office Phone: 604-712-3390, Cell: 604-947-2164, Email: ted@resinworkshub.ca

Colors

Designer to choose only greyscale colors for use in the design.

```html
<!DOCTYPE html>
<html lang="en">
<head>
<meta charset="utf-8">
<title>Resin Works Hub — Business Card</title>
<link href="https://fonts.googleapis.com/css2?family=Poppins:wght@300;400;700&display=swap" rel="stylesheet">
<style>
  :root {
    --stage: #1e1e1f;
    --card: #222225;
    --ink: #ffffff;
    --muted: #d9d9d9;
    --rule: #8a8a8a;
    --pattern-dark: #1a1a1c;
    --pattern-light: #3a3a3d;
  }
  * { margin: 0; padding: 0; box-sizing: border-box; }
  html, body { width: 1200px; height: 711px; overflow: hidden; }
  body {
    background: var(--stage);
    font-family: "Poppins", sans-serif;
    color: var(--ink);
    position: relative;
  }
  .card {
    position: absolute;
    width: 540px;
    height: 309px;
    background: var(--card);
    border-radius: 3px;
    overflow: hidden;
  }
  .card--front { left: 40px; top: 201px; }
  .card--back { left: 620px; top: 201px; }

  .pattern {
    position: absolute; inset: 0;
    background: linear-gradient(135deg, var(--pattern-dark) 0%, var(--pattern-light) 55%, var(--pattern-dark) 100%);
  }
  .brand {
    position: absolute;
    font-weight: 700;
    text-transform: uppercase;
    color: var(--ink);
    letter-spacing: 1px;
    text-align: center;
    line-height: 1.05;
  }
  .card--front .brand {
    left: 0; right: 0; top: 50%;
    transform: translateY(-50%);
    font-size: 40px;
  }
  .card--back .brand {
    left: 24px; width: 220px; top: 98px;
    font-size: 30px;
  }

  .divider {
    position: absolute;
    left: 270px; top: 58px;
    width: 1px; height: 150px;
    background: var(--rule);
  }
  .person {
    position: absolute;
    left: 292px; top: 52px;
  }
  .person__name { font-size: 24px; font-weight: 300; line-height: 1.1; }
  .person__name b { font-weight: 700; }
  .person__title { font-size: 12px; font-weight: 400; color: var(--muted); margin-top: 2px; }

  .contact-list {
    list-style: none;
    position: absolute;
    left: 292px; top: 118px;
  }
  .contact-list li {
    display: flex; align-items: center; gap: 8px;
    font-size: 12px; font-weight: 300;
    height: 20px;
  }
  .contact-list svg { width: 12px; height: 12px; flex: none; }

  .address {
    position: absolute;
    left: 0; right: 0; bottom: 26px;
    text-align: center;
    font-size: 13px; font-weight: 300;
  }
</style>
</head>
<body>

<section class="card card--front">
  <div class="pattern" role="img" aria-label="Repeating embossed chevron pattern in dark grey tones"></div>
  <div class="brand">Resin Works Hub</div>
</section>

<section class="card card--back">
  <div class="brand">Resin<br>Works Hub</div>
  <div class="divider"></div>

  <div class="person">
    <p class="person__name"><b>Ted</b> Galloway</p>
    <p class="person__title">Founder &amp; CEO</p>
  </div>

  <ul class="contact-list">
    <li>
      <svg viewBox="0 0 24 24" fill="#fff"><path d="M6.6 10.8a15.1 15.1 0 0 0 6.6 6.6l2.2-2.2a1 1 0 0 1 1-.25 11.4 11.4 0 0 0 3.6.57 1 1 0 0 1 1 1V20a1 1 0 0 1-1 1A17 17 0 0 1 3 4a1 1 0 0 1 1-1h3.5a1 1 0 0 1 1 1c0 1.25.2 2.45.57 3.57a1 1 0 0 1-.25 1z"/></svg>
      604-712-3390
    </li>
    <li>
      <svg viewBox="0 0 24 24" fill="none" stroke="#fff" stroke-width="2"><rect x="6" y="2" width="12" height="20" rx="2"/><line x1="11" y1="18" x2="13" y2="18"/></svg>
      604-947-2164
    </li>
    <li>
      <svg viewBox="0 0 24 24" fill="none" stroke="#fff" stroke-width="2"><circle cx="12" cy="12" r="10"/><path d="M2 12h20M12 2a15 15 0 0 1 0 20M12 2a15 15 0 0 0 0 20"/></svg>
      www.resinworkshub.ca
    </li>
    <li>
      <svg viewBox="0 0 24 24" fill="none" stroke="#fff" stroke-width="2"><rect x="2" y="5" width="20" height="14" rx="1"/><path d="M2 6l10 7 10-7"/></svg>
      ted@resinworkshub.ca
    </li>
  </ul>

  <p class="address">7-4812 Fernhollow Road, Abbotsford, BC, V3K 8R2.</p>
</section>

</body>
</html>
```